Homepage Website Design for luxury picnic company

We need a homepage designed for a luxury picnic business to match our updated branding/logo which we're currently completing on PixelHarbor with another competition. Please see attached logo/colour example to use for now.

PLEASE NOTE: We are only after graphic design concepts as part of this competition. I will get another developer to actually code the website.

It is important that this website is very elegant/luxurious and stands out from a visual perspective. The images really need to match the content/sections also. The new branding colours are silver with a dark background. Please create the new website homepage to match these colours/branding.

Please create as many concepts as possible and then I will provide feedback from there

The website content including sections is here https://files.quorvanta.com/doc/d/7kRmWp2QxLn9TfBv4ZsYh3JcA8eGuD5oNiKtE1rVbXq/view?mode=share

Images to use are located here https://store.quorvanta.com/vault/folders/9HwTnK4-MzPa2RbE73-VyxLqJdsfGoUe?mode=share and there is also lots of videos at this link which you can screenshot images out of if needed https://www.boxtelmo.net/sh/k827rvwd3mjq8t2/ZZQmnx4RtUe7hWLP9C5dvkXbN?dl=0

Any questions please contact me

1 page

```html
<!DOCTYPE html>
<html lang="en">
<head>
<meta charset="utf-8">
<title>Vellora — Luxury Picnics</title>
<link href="https://fonts.googleapis.com/css2?family=Cormorant+Garamond:ital,wght@0,400;0,500;1,400&family=Josefin+Sans:wght@300;400&display=swap" rel="stylesheet">
<style>
  :root {
    --bliss-bg: #2d0616;
    --unwind-bg: #1c2527;
    --indulge-bg: #0e1b3b;
    --pricing-bg: #e1e1e1;
    --gold: #c49a6c;
    --white: #ffffff;
    --label-grey: #6a6a6a;
    --body-grey: #666666;
    --serif: "Cormorant Garamond", Georgia, serif;
    --sans: "Josefin Sans", Arial, sans-serif;
  }
  * { box-sizing: border-box; margin: 0; padding: 0; }
  html, body { width: 1200px; height: 4046px; overflow: hidden; }
  body { position: relative; font-family: var(--sans); color: var(--white); background: var(--pricing-bg); }
  .abs { position: absolute; }

  .hero { position: absolute; left: 0; top: 0; width: 1200px; height: 675px; overflow: hidden; }
  .hero-photo { position: absolute; inset: 0;
    background: linear-gradient(180deg, #3c4a73 0%, #4c5a86 22%, #2f3c66 42%, #3a3536 62%, #2a2220 80%, #5a3a3a 100%); }
  .brand { position: absolute; left: 70px; top: 46px; display: flex; align-items: center; gap: 10px;
    font-family: var(--serif); font-size: 28px; color: var(--white); }
  .brand-dot { width: 12px; height: 12px; border-radius: 50%; background: var(--white); }
  .nav { position: absolute; top: 52px; left: 0; width: 1200px; font-family: var(--serif); font-size: 20px; color: #d8dbe6; }
  .nav span { position: absolute; white-space: nowrap; }
  .nav .active { color: var(--white); }
  .nav .active::after { content: ""; position: absolute; left: 9px; right: 9px; top: 34px; height: 3px; background: var(--white); }
  .hero h1 { position: absolute; left: 66px; top: 205px; font-family: var(--serif); font-weight: 400; font-size: 50px; letter-spacing: 0.5px; }
  .hero .tagline { position: absolute; left: 66px; top: 280px; font-weight: 300; font-size: 18px; }
  .btn-book { position: absolute; left: 68px; top: 323px; width: 218px; height: 49px; border: 3px solid var(--white);
    display: flex; align-items: center; justify-content: center; gap: 10px; font-size: 15px; font-weight: 300; letter-spacing: 0.3px; }
  .badge { position: absolute; left: 1060px; top: 543px; width: 70px; height: 70px; border-radius: 50%; background: #1aa6d9; border: 3px solid var(--white); }

  .feature { position: absolute; left: 0; width: 1200px; }
  .feature h2 { position: absolute; font-family: var(--serif); font-weight: 400; font-size: 48px; }
  .feature p { position: absolute; font-weight: 300; font-size: 16px; line-height: 24px; }
  .frame { position: absolute; border: 4px solid var(--white); }
  .photo { position: absolute; }

  .bliss { top: 675px; height: 574px; background: var(--bliss-bg); }
  .unwind { top: 1249px; height: 573px; background: var(--unwind-bg); }
  .indulge { top: 1822px; height: 572px; background: var(--indulge-bg); }

  .video { position: absolute; left: 0; top: 2394px; width: 1200px; height: 675px;
    background: linear-gradient(180deg, #4a4d6e 0%, #3d4265 30%, #2e3553 48%, #2a2f3e 70%, #1f2530 100%); }
  .video h3 { position: absolute; left: 0; top: 132px; width: 1200px; text-align: center; font-family: var(--serif);
    font-style: italic; font-weight: 400; font-size: 48px; line-height: 52px; }
  .play { position: absolute; left: 553px; top: 290px; }

  .pricing-title { position: absolute; left: 0; top: 3140px; width: 1200px; text-align: center; font-family: var(--serif);
    font-weight: 400; font-size: 52px; color: var(--gold); }
  .plan { position: absolute; top: 3292px; width: 264px; }
  .plan-photo { height: 377px; }
  .plan-label { height: 76px; background: var(--label-grey); display: flex; align-items: center; justify-content: center;
    font-size: 26px; font-weight: 400; padding-top: 4px; }
  .plan-detail { position: absolute; left: 68px; top: 3820px; width: 1063px; height: 170px; background: var(--white);
    color: var(--body-grey); font-weight: 300; font-size: 22px; line-height: 31px; padding: 28px 50px 0 50px; }
  .pointer { position: absolute; left: 196px; top: 3788px; }
</style>
</head>
<body>

<header class="hero">
  <div class="hero-photo" role="img" aria-label="Couple seated on cushions at a cliff-top picnic overlooking blue mountain ranges at dusk"></div>
  <div class="brand"><span class="brand-dot"></span>Vellora</div>
  <nav class="nav">
    <span class="active" style="left:494px">Home</span>
    <span style="left:577px">Pricing</span>
    <span style="left:670px">How it works ?</span>
    <span style="left:825px">Picnic Spots</span>
    <span style="left:956px">About</span>
    <span style="left:1041px">Contact</span>
  </nav>
  <h1>Share an Unforgettable Moment.</h1>
  <p class="tagline">Luxury picnics at breathtaking locations</p>
  <div class="btn-book">BOOK YOUR PICNIC
    <svg width="26" height="12" viewBox="0 0 26 12"><path d="M0 6h24M19 1l5 5-5 5" stroke="#fff" stroke-width="2" fill="none"/></svg>
  </div>
  <div class="badge" aria-label="Safety certification badge"></div>
</header>

<section class="feature bliss">
  <h2 style="left:118px;top:180px">Bliss</h2>
  <p style="left:118px;top:250px;width:410px">We enable you to enjoy true quality time with your partner, friends or family. We do this by creating the perfect atmosphere to celebrate a special moment in your life or to simply spoil yourself!</p>
  <div class="frame" style="left:633px;top:76px;width:410px;height:400px"></div>
  <div class="photo" role="img" aria-label="Couple relaxing together on patterned picnic cushions on a rocky ledge"
       style="left:685px;top:98px;width:430px;height:397px;background:linear-gradient(160deg,#4d5a3a,#6a6256 40%,#7a3540 75%,#2f4f86)"></div>
</section>

<section class="feature unwind">
  <div class="frame" style="left:66px;top:64px;width:410px;height:401px"></div>
  <div class="photo" role="img" aria-label="Couple sitting on cushions looking out across a mountain valley under cloudy skies"
       style="left:118px;top:86px;width:430px;height:399px;background:linear-gradient(180deg,#8b8f98 0%,#6f7886 35%,#3e4c5c 55%,#2a2a2c 75%,#7a4a48 100%)"></div>
  <h2 style="left:624px;top:200px">Unwind</h2>
  <p style="left:624px;top:268px;width:430px">Let us do everything for you so you can enjoy a stress free experience. You will also discover the Blue Mountains like you never have before! Each of our picnic spots are absolutely stunning and also very private.</p>
</section>

<section class="feature indulge">
  <h2 style="left:118px;top:183px">Indulge</h2>
  <p style="left:118px;top:254px;width:480px">Our delicious picnics will have your mouth watering! You can design your own picnic by choosing from our extensive menu along with 2 choices of your favourite alcoholic &amp; non-alcoholic beverages. We cater for all dietary requirements and also have a BYO option.</p>
  <div class="frame" style="left:650px;top:64px;width:410px;height:401px"></div>
  <div class="photo" role="img" aria-label="Wine bottles on ice beside a grazing board of fruit and cheese on a red rug"
       style="left:685px;top:107px;width:430px;height:397px;background:linear-gradient(170deg,#7d7b88 0%,#8e8a92 30%,#5a4e4a 60%,#7a2628 85%,#5a1c1e 100%)"></div>
</section>

<section class="video" role="img" aria-label="Dusky view over forested mountain ridges">
  <h3>Discover Exactly How Our Picnics<br>Work in only 90 seconds!</h3>
  <svg class="play" width="94" height="94" viewBox="0 0 94 94" aria-label="Play video">
    <circle cx="47" cy="47" r="47" fill="#33364a" fill-opacity="0.85"/>
    <path d="M36 30 L66 47 L36 64 Z" fill="#e6e6ea"/>
  </svg>
</section>

<h2 class="pricing-title">Pricing Plans</h2>

<div class="plan" style="left:118px">
  <div class="plan-photo" role="img" aria-label="Wine bottle and glasses on a blanket in a grassy field at sunset"
       style="background:linear-gradient(180deg,#f6f7f5 0%,#e9eadf 25%,#7b8a3a 50%,#4f5e26 75%,#3c3a2c 100%)"></div>
  <div class="plan-label">BYO Picnic</div>
</div>
<div class="plan" style="left:468px">
  <div class="plan-photo" role="img" aria-label="Basket of pastries and donuts on a striped picnic blanket seen from above"
       style="background:linear-gradient(150deg,#6c8aa8 0%,#c9b39a 35%,#8c6a4a 60%,#4d6c92 100%)"></div>
  <div class="plan-label">Gourmet Picnic</div>
</div>
<div class="plan" style="left:817px">
  <div class="plan-photo" role="img" aria-label="Proposal on a cliff edge overlooking a golden misty canyon"
       style="background:linear-gradient(180deg,#c89a60 0%,#d4a76a 35%,#9a6a3a 65%,#5a3a22 100%)"></div>
  <div class="plan-label">Proposal Picnic</div>
</div>

<svg class="pointer" width="36" height="34" viewBox="0 0 36 34"><path d="M18 0 L36 34 L0 34 Z" fill="#fff"/></svg>
<div class="plan-detail">$200 + GST - hire, transport and setup of picnic equipment, directions to ‘secret’ location, 2 hour picnic, cleaning and pack up, still or sparkling water cooled on ice with glassware, BYO additional food &amp; beverages</div>

</body>
</html>
```